Kestrel Facilities Business Card Design

We would now like to design business cards with the new Kestrel Facilities logo

Target Market(s)

Professional

Industry/Entity Type

Professional services

Contact Information for Business Card

Employee name, title, phone number, email address, corporate office address and logo.

Font styles to use
Sans Serif

Colors
0054AA
0677BA
7BADD7
CADEEF
E8F1F8

Requirements
Must have
• My logo
Should not have
• any other pictures or images besides my logo

```html
<!DOCTYPE html>
<html lang="en">
<head>
<meta charset="UTF-8">
<title>Kestrel Facilities Business Card</title>
<link href="https://fonts.googleapis.com/css2?family=Montserrat:wght@400;500;700&display=swap" rel="stylesheet">
<style>
  :root {
    --brand-blue: #3577c2;
    --deep-blue: #0054AA;
    --ink: #1d1d1f;
    --paper: #ffffff;
    --stage: #8e8e8e;
    --rule-grey: #c9c9c9;
  }
  * { box-sizing: border-box; margin: 0; padding: 0; }
  html, body { width: 1200px; height: 900px; overflow: hidden; }
  body {
    background: radial-gradient(circle at 45% 40%, #c4c4c4 0%, var(--stage) 70%, #5c5c5c 100%);
    font-family: "Montserrat", sans-serif;
    position: relative;
  }
  .card {
    position: absolute;
    width: 630px;
    height: 360px;
    background: var(--paper);
    border-radius: 28px;
    overflow: hidden;
    box-shadow: 0 10px 28px rgba(0,0,0,0.35);
  }
  .card--front { left: 110px; top: 60px; }
  .card--back { left: 460px; top: 480px; }

  .wordmark {
    display: flex;
    align-items: center;
    gap: 14px;
    color: var(--brand-blue);
    font-weight: 700;
    text-transform: uppercase;
    line-height: 1.05;
  }
  .wordmark__square {
    background: var(--brand-blue);
    flex: none;
  }
  .card--front .wordmark {
    position: absolute;
    left: 50%; top: 50%;
    transform: translate(-50%, -50%);
    font-size: 40px;
  }
  .card--front .wordmark__square { width: 56px; height: 56px; }

  .card--back .wordmark {
    position: absolute;
    left: 40px; top: 118px;
    font-size: 28px;
  }
  .card--back .wordmark__square { width: 40px; height: 40px; }

  .divider {
    position: absolute;
    left: 300px; top: 70px;
    width: 2px; height: 170px;
    background: var(--brand-blue);
  }
  .contact {
    position: absolute;
    left: 326px; top: 56px;
    color: var(--ink);
  }
  .contact__name {
    color: var(--brand-blue);
    font-weight: 700;
    font-size: 22px;
    letter-spacing: 0.3px;
  }
  .contact__title { font-size: 15px; margin-top: 2px; }
  .contact__address { font-size: 14px; margin-top: 14px; line-height: 1.4; }
  .contact__lines { list-style: none; margin-top: 14px; font-size: 14px; }
  .contact__lines li { display: flex; align-items: center; gap: 10px; line-height: 1.6; }
  .contact__lines svg { width: 16px; height: 16px; fill: var(--brand-blue); }

  .footer-art { position: absolute; left: 0; bottom: 0; width: 630px; height: 110px; }
  .web {
    position: absolute;
    right: 34px; bottom: 22px;
    color: var(--paper);
    font-size: 14px;
    letter-spacing: 0.3px;
  }
</style>
</head>
<body>
  <section class="card card--front" aria-label="Card front">
    <div class="wordmark"><span class="wordmark__square"></span><span>Kestrel<br>Facilities</span></div>
  </section>

  <section class="card card--back" aria-label="Card back">
    <div class="wordmark"><span class="wordmark__square"></span><span>Kestrel<br>Facilities</span></div>
    <div class="divider"></div>
    <div class="contact">
      <p class="contact__name">DANA WHITLOCK</p>
      <p class="contact__title">Co-Founder</p>
      <p class="contact__address">4180 N. Harbor Lane<br>Suite 210 Eastvale.42</p>
      <ul class="contact__lines">
        <li>
          <svg viewBox="0 0 24 24" aria-hidden="true"><path d="M6.6 10.8a15 15 0 0 0 6.6 6.6l2.2-2.2a1 1 0 0 1 1-.25 11.4 11.4 0 0 0 3.6.57 1 1 0 0 1 1 1V20a1 1 0 0 1-1 1A17 17 0 0 1 3 4a1 1 0 0 1 1-1h3.5a1 1 0 0 1 1 1c0 1.25.2 2.45.57 3.6a1 1 0 0 1-.25 1z"/></svg>
          +254-301-47225
        </li>
        <li>
          <svg viewBox="0 0 24 24" aria-hidden="true"><path d="M2 5h20v14H2z M2 5l10 8 10-8" fill="none" stroke="#3577c2" stroke-width="2"/></svg>
          info@kestrelfm.com
        </li>
      </ul>
    </div>
    <svg class="footer-art" viewBox="0 0 630 110" aria-hidden="true">
      <polygon points="0,96 430,58 430,110 0,110" fill="#c9c9c9"/>
      <line x1="0" y1="94" x2="430" y2="56" stroke="#3577c2" stroke-width="2"/>
      <polygon points="430,46 630,20 630,110 430,110" fill="#3577c2"/>
    </svg>
    <p class="web">www.kestrelfm.com</p>
  </section>
</body>
</html>
```